Brightlane Rapid Rinse Web Design

We are looking for a web design that highlights our state of the art fully automated commercial vehicle washing equipment. Similar system to a car wash however this system is meant for the largest vehicles on our roadways. Transport trucks with or without a trailer, busses both highway and school, RV's from 5th wheel type to A Class. Cement trucks, dump trucks, vac trucks, fuel trucks etc. Pick ups with utility trailers...Refrigerator truck clean outs.
Brightlane Rapid Rinse will wash your vehicle quickly and with a minimal impact on the environment

Home page
About us
Why Brightlane
Services and pricing
Videos of wash system
Fleets
contact us

Target Market(s)

Commercial vehicle owners and operators as well as corporate fleets. Includes busses, municipal, school and highway.both school and

Industry/Entity Type

transportation

Coding

Coded - Design and coding required

Number of Pages Required

5+ page

Font styles to use
Sans Serif

Colors
0054AA
0677BA
7BADD7
CADEEF
E8F1F8

Requirements
Must have
• Welcome page,why us page which describes the financial and environmental benefits. payment processing page, contact us page, Services which is washing vehicles and greasing for commercial vehicles that want that service and grease
Nice to have
• pictures of both clean and dirty commercial vehicles ie. before and after

```html
<!DOCTYPE html>
<html lang="en">
<head>
<meta charset="utf-8">
<title>Brightlane Rapid Rinse</title>
<link href="https://fonts.googleapis.com/css2?family=Krona+One&family=IBM+Plex+Sans:wght@400;500;600&display=swap" rel="stylesheet">
<style>
:root{
  --blue-deep:#0054AA;
  --blue-mid:#0677BA;
  --blue-soft:#7BADD7;
  --blue-pale:#CADEEF;
  --blue-mist:#E8F1F8;
  --ink:#111;
  --text:#333;
  --muted:#888;
  --band:#f6f6f6;
  --black:#000;
  --white:#fff;
  --star:#f2a900;
}
*{margin:0;padding:0;box-sizing:border-box}
html,body{width:1200px;height:3369px;overflow:hidden}
body{position:relative;font-family:"IBM Plex Sans",sans-serif;color:var(--text);background:var(--white)}
.display{font-family:"Krona One",sans-serif;text-transform:uppercase;color:var(--ink)}
.abs{position:absolute}
.btn{position:absolute;display:flex;align-items:center;justify-content:center;font-family:"Krona One",sans-serif;text-transform:uppercase;border-radius:6px}

/* header */
.site-header{left:0;top:0;width:1200px;height:82px;background:var(--white);z-index:2}
.brand{left:110px;top:16px}
.brand .name{font-family:"Krona One",sans-serif;font-size:26px;color:var(--ink);letter-spacing:1px;line-height:30px}
.brand .sub{font-family:"Krona One",sans-serif;font-size:14px;color:var(--blue-deep);letter-spacing:13px;line-height:18px;margin-top:2px}
.nav{right:110px;top:30px;display:flex;gap:39px;font-size:13px;color:var(--ink)}

/* hero */
.hero{left:0;top:82px;width:1200px;height:600px;background:linear-gradient(100deg,#1f4fa8 0%,#283a5a 35%,#1a2230 65%,#2b3340 100%)}
.hero-copy{left:110px;top:163px}
.hero-copy .pre{font-size:32px;line-height:40px;color:var(--white)}
.hero-copy h1{font-size:60px;line-height:74px;color:var(--white);margin-top:4px}
.hero .b1{left:111px;top:374px;width:208px;height:52px;background:var(--blue-deep);color:var(--white);font-size:15px}
.hero .b2{left:335px;top:374px;width:190px;height:52px;background:var(--blue-deep);color:var(--white);font-size:15px}
.hero .b3{left:540px;top:374px;width:190px;height:52px;background:var(--white);color:var(--blue-deep);font-size:15px}

/* mission */
.mission-title{left:110px;top:752px;font-size:33px}
.hex{left:127px;top:805px;width:433px;height:475px}
.mission-text{left:653px;top:818px;width:440px;font-size:15px;line-height:25.7px;color:var(--text)}
.mission-text p{margin-bottom:25.7px}
.mission-btn{left:650px;top:1199px;width:220px;height:55px;background:var(--blue-deep);color:var(--white);font-size:16px}

/* industries */
.band{left:0;top:1386px;width:1200px;height:664px;background:var(--band)}
.ind-title{left:110px;top:1481px;font-size:33px}
.card{position:absolute;border-radius:12px;overflow:hidden}
.card .label{position:absolute;left:27px;bottom:26px;font-family:"Krona One",sans-serif;color:var(--white);font-size:16px;line-height:21px;text-transform:uppercase}
.c1{left:110px;top:1579px;width:288px;height:358px;background:linear-gradient(180deg,#6c6f66,#4b4d47 60%,#3c3d3a)}
.c3{left:801px;top:1579px;width:287px;height:358px;background:linear-gradient(180deg,#7a8a9a 0%,#9a6a3a 40%,#2b5c6a 70%,#283640)}
.c2{left:444px;top:1567px;width:311px;height:379px;background:var(--white);box-shadow:0 4px 18px rgba(0,0,0,.09)}
.c2 .photo{position:absolute;left:11px;top:11px;width:289px;height:206px;border-radius:10px;background:linear-gradient(100deg,#3a3a36,#8d8e88 55%,#d8d8d4)}
.c2 h3{position:absolute;left:21px;top:241px;font-size:15.5px}
.c2 p{position:absolute;left:21px;top:270px;width:265px;font-size:12.5px;line-height:21.5px;color:var(--text)}
.c2 .more{position:absolute;left:25px;top:344px;font-family:"Krona One",sans-serif;font-size:12px;color:var(--blue-deep);display:flex;align-items:center;gap:5px;text-transform:uppercase}

/* testimonials */
.say-title{left:0;top:2138px;width:1262px;text-align:center;font-size:34px}
.review{position:absolute;top:2236px;width:562px;height:218px;background:var(--white);box-shadow:0 2px 14px rgba(0,0,0,.06)}
.review .avatar{position:absolute;left:21px;top:18px;width:50px;height:50px;border-radius:50%;background:linear-gradient(135deg,#c9a58a,#6b5648)}
.review h4{position:absolute;left:95px;top:26px;font-family:"Krona One",sans-serif;font-size:17px;color:var(--ink)}
.review .date{position:absolute;left:95px;top:52px;font-size:12px;color:var(--muted)}
.review p{position:absolute;left:96px;top:76px;width:450px;font-size:12.5px;line-height:26px;color:var(--text)}
.review .stars{position:absolute;left:97px;top:166px;display:flex;gap:4px}
.r1{left:101px}.r2{left:726px}
.track{left:276px;top:2533px;width:649px;height:5px;border-radius:3px;background:#eee}
.thumb{left:431px;top:2533px;width:87px;height:6px;border-radius:3px;background:var(--blue-deep)}

/* contact band */
.footer{left:0;top:2779px;width:1200px;height:590px;background:var(--black)}
.cta{left:114px;top:2636px;width:976px;height:278px;border-radius:24px;background:linear-gradient(180deg,#1a7cc6,#0f6fb8);text-align:center}
.cta h2{font-family:"Krona One",sans-serif;font-size:34px;color:var(--white);margin-top:40px}
.cta p{width:700px;margin:22px auto 0;font-size:15px;line-height:24px;color:var(--white)}
.cta .btn{left:393px;top:192px;width:185px;height:46px;background:var(--blue-deep);color:var(--white);font-size:14px}

.fcol{position:absolute;top:3014px;color:var(--white)}
.fcol h5{font-family:"Krona One",sans-serif;font-size:15px;text-transform:uppercase;color:var(--white)}
.fcol h5::after{content:"";display:block;width:30px;height:2px;background:var(--blue-deep);margin-top:10px}
.fcol ul{list-style:none;margin-top:20px;font-size:15px}
.f1{left:114px}.f2{left:456px}.f3{left:683px}.f4{left:844px}
.f1 li{display:flex;gap:9px;margin-bottom:13px;line-height:26px}
.f1 li svg{margin-top:6px;flex:none}
.f2 li,.f3 li{display:flex;align-items:center;gap:10px;height:30px}
.dot{width:11px;height:11px;border-radius:50%;background:var(--white)}
.field{width:242px;height:50px;border-bottom:1px solid #666;font-size:14px;color:#ccc;padding-top:16px;margin-top:-2px}
.f4 .btn{position:absolute;left:2px;top:170px;width:145px;height:38px;border-radius:20px;background:var(--blue-deep);color:var(--white);font-size:12px}
.rule{left:114px;top:3263px;width:976px;height:1px;background:#2a2a2a}
.copy{left:0;top:3296px;width:1200px;text-align:center;font-size:15px;color:var(--white)}
</style>
</head>
<body>

<header class="abs site-header">
  <div class="abs brand">
    <div class="name">BRIGHTLANE</div>
    <div class="sub">RAPID RINSE</div>
  </div>
  <nav class="abs nav"><span>Home</span><span>About Us</span><span>Why Brightlane</span><span>Services</span><span>Pricing</span><span>More</span></nav>
</header>

<section class="abs hero">
  <div class="abs" style="inset:0" role="img" aria-label="Worker pressure-washing a blue transport truck at night"></div>
  <div class="abs hero-copy">
    <div class="pre display">Welcome to</div>
    <h1 class="display">Brightlane<br>Rapid Rinse</h1>
  </div>
  <div class="btn b1">Book a wash</div>
  <div class="btn b2">Learn more</div>
  <div class="btn b3">Contact us</div>
</section>

<h2 class="abs display mission-title">Mission Statement</h2>
<svg class="abs hex" viewBox="0 0 433 475" role="img" aria-label="Blue semi truck inside the wash bay">
  <defs><linearGradient id="hexfill" x1="0" y1="0" x2="1" y2="1"><stop offset="0" stop-color="#cfd6dc"/><stop offset=".45" stop-color="#1f5fb5"/><stop offset="1" stop-color="#2a2e33"/></linearGradient></defs>
  <polygon points="216,0 433,118 433,357 216,475 0,357 0,118" fill="url(#hexfill)"/>
</svg>
<div class="abs mission-text">
  <p>Lorem ipsum dolor sit amet, consectetur adipiscing elit, sed do eiusmod tempor incididunt ut labore et dolore magna aliqua. Quis ipsum suspendisse ultrices gravida. Risus commodo viverra maecenas accumsan lacus vel facilisis.</p>
  <p>Lorem ipsum dolor sit amet, consectetur adipiscing elit, sed do eiusmod tempor incididunt ut labore et dolore magna aliqua. Quis ipsum suspendisse ultrices gravida. Risus commodo viverra maecenas accumsan lacus vel facilisis.</p>
  <p>Lorem ipsum dolor sit amet, consectetur adipiscing elit, sed do eiusmod tempor incididunt ut labore et dolore magna aliqua. Quis ipsum suspendisse ultrices gravida. Risus commodo viverra maecenas accumsan lacus vel facilisis.</p>
</div>
<div class="btn mission-btn">Learn more</div>

<section class="abs band"></section>
<h2 class="abs display ind-title">The Industries</h2>
<div class="card c1" role="img" aria-label="White truck leaving an automated wash tunnel"><div class="label">Automated<br>truck wash</div></div>
<div class="card c2">
  <div class="photo" role="img" aria-label="Worker cleaning beside a white truck in a tiled wash bay"></div>
  <h3 class="display">Additional Services</h3>
  <p>Lorem ipsum dolor sit amet, consectetur adipiscing elit, sed do eiusmod tempor incididunt ut labore et dolore magna aliqua.</p>
  <div class="more">Learn more <svg width="11" height="11" viewBox="0 0 12 12"><circle cx="6" cy="6" r="6" fill="#0054AA"/><path d="M5 3.5 7.5 6 5 8.5" stroke="#fff" stroke-width="1.6" fill="none"/></svg></div>
</div>
<div class="card c3" role="img" aria-label="Row of parked fleet trucks at dusk"><div class="label">Fleet services</div></div>

<h2 class="abs display say-title">What our members say</h2>
<div class="review r1">
  <div class="avatar" role="img" aria-label="Member portrait"></div>
  <h4>JORDAN WHITFIELD</h4>
  <div class="date">2024-02-27</div>
  <p>Lorem ipsum dolor sit amet, consectetur adipiscing elit, sed do eiusmod tempor incididunt ut labore et dolore magna aliqua. Quis ipsum suspendisse ultrices gravida. Risus commodo viverra maecenas accumsan lacus vel</p>
  <div class="stars">
    <svg width="9" height="9" viewBox="0 0 10 10"><path d="M5 0l1.5 3.2 3.5.4-2.6 2.4.7 3.5L5 7.8 1.9 9.5l.7-3.5L0 3.6l3.5-.4z" fill="#f2a900"/></svg>
    <svg width="9" height="9" viewBox="0 0 10 10"><path d="M5 0l1.5 3.2 3.5.4-2.6 2.4.7 3.5L5 7.8 1.9 9.5l.7-3.5L0 3.6l3.5-.4z" fill="#f2a900"/></svg>
    <svg width="9" height="9" viewBox="0 0 10 10"><path d="M5 0l1.5 3.2 3.5.4-2.6 2.4.7 3.5L5 7.8 1.9 9.5l.7-3.5L0 3.6l3.5-.4z" fill="#f2a900"/></svg>
    <svg width="9" height="9" viewBox="0 0 10 10"><path d="M5 0l1.5 3.2 3.5.4-2.6 2.4.7 3.5L5 7.8 1.9 9.5l.7-3.5L0 3.6l3.5-.4z" fill="#f2a900"/></svg>
    <svg width="9" height="9" viewBox="0 0 10 10"><path d="M5 0l1.5 3.2 3.5.4-2.6 2.4.7 3.5L5 7.8 1.9 9.5l.7-3.5L0 3.6l3.5-.4z" fill="#f2a900"/></svg>
  </div>
</div>
<div class="review r2">
  <div class="avatar" role="img" aria-label="Member portrait"></div>
  <h4>JORDAN WHITFIELD</h4>
  <div class="date">2024-02-27</div>
  <p>Lorem ipsum dolor sit amet, consectetur adipiscing elit, sed do eiusmod tempor incididunt ut labore et dolore magna aliqua. Quis ipsum suspendisse ultrices gravida. Risus commodo viverra maecenas accumsan lacus vel</p>
  <div class="stars">
    <svg width="9" height="9" viewBox="0 0 10 10"><path d="M5 0l1.5 3.2 3.5.4-2.6 2.4.7 3.5L5 7.8 1.9 9.5l.7-3.5L0 3.6l3.5-.4z" fill="#f2a900"/></svg>
    <svg width="9" height="9" viewBox="0 0 10 10"><path d="M5 0l1.5 3.2 3.5.4-2.6 2.4.7 3.5L5 7.8 1.9 9.5l.7-3.5L0 3.6l3.5-.4z" fill="#f2a900"/></svg>
    <svg width="9" height="9" viewBox="0 0 10 10"><path d="M5 0l1.5 3.2 3.5.4-2.6 2.4.7 3.5L5 7.8 1.9 9.5l.7-3.5L0 3.6l3.5-.4z" fill="#f2a900"/></svg>
    <svg width="9" height="9" viewBox="0 0 10 10"><path d="M5 0l1.5 3.2 3.5.4-2.6 2.4.7 3.5L5 7.8 1.9 9.5l.7-3.5L0 3.6l3.5-.4z" fill="#f2a900"/></svg>
    <svg width="9" height="9" viewBox="0 0 10 10"><path d="M5 0l1.5 3.2 3.5.4-2.6 2.4.7 3.5L5 7.8 1.9 9.5l.7-3.5L0 3.6l3.5-.4z" fill="#f2a900"/></svg>
  </div>
</div>
<div class="abs track"></div>
<div class="abs thumb"></div>

<footer class="abs footer"></footer>
<section class="abs cta" role="img" aria-label="Contact banner over a faint truck wash scene">
  <h2>CONTACT US</h2>
  <p>Lorem ipsum dolor sit amet, consectetur adipiscing elit, sed do eiusmod tempor incididunt ut labore et dolore magna aliqua. Quis ipsum suspendisse ultrices gravida. Risus commodo viverra maecenas accumsan lacus vel facilisis.</p>
  <div class="btn">Contact us</div>
</section>

<div class="fcol f1">
  <h5>Contact</h5>
  <ul>
    <li><svg width="10" height="13" viewBox="0 0 10 13"><path d="M5 0a5 5 0 0 0-5 5c0 3.5 5 8 5 8s5-4.5 5-8a5 5 0 0 0-5-5zm0 7a2 2 0 1 1 0-4 2 2 0 0 1 0 4z" fill="#0677BA"/></svg><span>Lorem ipsum dolor<br>sit amet</span></li>
    <li><svg width="12" height="12" viewBox="0 0 12 12"><path d="M2.5 0 4.5 2.5 3.3 4a7 7 0 0 0 4.7 4.7L9.5 7.5 12 9.5 10.5 12C5 12 0 7 0 1.5z" fill="#0677BA"/></svg><span>+1 555 014 2290</span></li>
    <li><svg width="13" height="10" viewBox="0 0 13 10"><rect width="13" height="10" rx="1" fill="#0677BA"/><path d="M0 1l6.5 4.5L13 1" stroke="#000" fill="none"/></svg><span>hello@brightlanerapidrinse.com</span></li>
  </ul>
</div>
<div class="fcol f2">
  <h5>Help Link</h5>
  <ul>
    <li><svg width="6" height="9" viewBox="0 0 6 9"><path d="M1 1l3.5 3.5L1 8" stroke="#fff" stroke-width="1.4" fill="none"/></svg>Terms &amp; Condtions</li>
    <li><svg width="6" height="9" viewBox="0 0 6 9"><path d="M1 1l3.5 3.5L1 8" stroke="#fff" stroke-width="1.4" fill="none"/></svg>Privacy Policy</li>
    <li><svg width="6" height="9" viewBox="0 0 6 9"><path d="M1 1l3.5 3.5L1 8" stroke="#fff" stroke-width="1.4" fill="none"/></svg>About Us</li>
    <li><svg width="6" height="9" viewBox="0 0 6 9"><path d="M1 1l3.5 3.5L1 8" stroke="#fff" stroke-width="1.4" fill="none"/></svg>Support</li>
  </ul>
</div>
<div class="fcol f3">
  <h5>Follow Us</h5>
  <ul>
    <li><span class="dot"></span>Community Page</li>
    <li><span class="dot"></span>Photo Feed</li>
    <li><span class="dot"></span>News Feed</li>
    <li><span class="dot"></span>Video Channel</li>
  </ul>
</div>
<div class="fcol f4">
  <h5>Newsletter Updates</h5>
  <div style="margin-top:12px;margin-left:3px">
    <div class="field">Name*</div>
    <div class="field">Email*</div>
  </div>
  <div class="btn">Submit now</div>
</div>
<div class="abs rule"></div>
<div class="abs copy">©Copyrights 2024&nbsp; Brightlane Rapid Rinse.&nbsp; |&nbsp;&nbsp; All Rights Reserved</div>

</body>
</html>
```